Voltharrow Power Product Distribution Brochure

We are looking to have our current brochure for our customers completely redesigned...the idea is to present the relevant information in an attractive way . Our website is voltharrowpower.example where you can find more information about us. We have included a file with a rough idea of the page order and what each should include but feel free to adapt based on design. The example provided is only for context and doesnt have to be maintained. We will be using the brochure both digitally and in print form. As long as it reads easily and is eye catching, the design can be horizontal or vertical.Final deliverable should be indesign file.

"Our Brands" page: should be limited to one page (space being enough) where it has the header for each one (for example diesel generators) space for one or two lines of text and then the corresponding logos for each of the five categories
Updates

For those asking: the "our brands" page should be a single page layout where there is a header with the corresponding section and space for maybe one line of text followed by the two logos for that category. Each of the product pages should be similar in fashion to the one in the document attached: a photo of the product with some white space and space for the text to be included. We will be posting additional examples today

Target Market(s)

We want to present it to customers both digitally and in print so they can see our products

Industry/Entity Type

Power Generation

Font styles to use
Serif

Requirements
Must have
• Eye catching and able to present the information in a presentable fashion. Rest is up to you.
Nice to have
• Should incorporate the colors of our logo but can also add other depending on design

```html
<!DOCTYPE html>
<html lang="en">
<head>
<meta charset="utf-8">
<title>Voltharrow Power — Distributor Program Guide</title>
<link href="https://fonts.googleapis.com/css2?family=Montserrat:wght@400;500;600;700;800&family=Lato:wght@400;700&display=swap" rel="stylesheet">
<style>
  :root {
    --gold: #f2b51c;
    --gold-deep: #e0a00f;
    --charcoal: #2b2b2b;
    --ink: #4a4546;
    --muted: #bdbdbd;
    --page: #eceeef;
    --page-shade: #d9dcdf;
    --canvas: #dcdcdc;
  }
  * { margin: 0; padding: 0; box-sizing: border-box; }
  html, body { width: 1200px; height: 900px; overflow: hidden; }
  body {
    background: var(--canvas);
    font-family: "Montserrat", sans-serif;
    color: var(--ink);
    position: relative;
  }
  .spread {
    position: absolute;
    left: 80px;
    width: 1040px;
    height: 400px;
    display: flex;
    box-shadow: 0 10px 24px rgba(0,0,0,.18);
  }
  .spread--cover { top: 28px; }
  .spread--products { top: 470px; }
  .page {
    position: relative;
    width: 520px;
    height: 400px;
    overflow: hidden;
    background: linear-gradient(135deg, #f4f5f6 0%, var(--page) 55%, var(--page-shade) 100%);
  }
  .page svg.page__art { position: absolute; inset: 0; }

  /* brand name */
  .brand { display: flex; align-items: center; gap: 8px; }
  .brand__mark { width: 16px; height: 16px; background: var(--gold); }
  .brand__name { font-weight: 600; font-size: 17px; letter-spacing: .5px; color: var(--ink); white-space: nowrap; }

  /* back cover */
  .back-cover__band { position: absolute; left: 0; right: 0; top: 180px; height: 130px; background: var(--charcoal); }
  .back-cover__frame { position: absolute; left: 60px; top: 40px; width: 400px; height: 320px; border: 2px solid var(--gold-deep); }
  .back-cover__brand { position: absolute; top: 120px; left: 0; right: 0; display: flex; justify-content: center; }
  .back-cover__contact { position: absolute; top: 202px; left: 0; right: 0; text-align: center; color: var(--gold); }
  .back-cover__title { font-weight: 600; font-size: 13px; margin-bottom: 18px; }
  .back-cover__line { font-size: 9px; line-height: 20px; }

  /* front cover */
  .front-cover__photo { position: absolute; left: 190px; top: 16px; width: 300px; height: 176px;
    background: linear-gradient(180deg, #9b9d9f 0%, #e3e4e5 45%, #6c6e70 100%); }
  .front-cover__brand { position: absolute; left: 40px; top: 252px; }
  .front-cover__brand .brand__name { color: var(--muted); }
  .front-cover__title { position: absolute; left: 250px; top: 212px; color: var(--gold); font-weight: 800; font-size: 24px; line-height: 25px; }
  .front-cover__sub { position: absolute; left: 250px; top: 292px; color: var(--muted); font-size: 8px; }
  .highlights { position: absolute; left: 30px; top: 340px; display: flex; gap: 22px; }
  .highlight { display: flex; flex-direction: column; align-items: center; width: 48px; text-align: center; font-size: 6px; line-height: 7px; color: var(--ink); text-transform: uppercase; }
  .highlight svg { width: 22px; height: 22px; margin-bottom: 3px; }

  /* product pages */
  .section-head { position: absolute; left: 0; top: 10px; width: 520px; display: flex; align-items: center; gap: 8px; }
  .section-head__rule { height: 2px; background: var(--gold); }
  .section-head__text { font-size: 22px; font-weight: 400; color: var(--ink); white-space: nowrap; }
  .section-head__text strong { font-weight: 700; }
  .product__block { position: absolute; width: 100px; height: 52px; background: var(--gold-deep); }
  .product__name { position: absolute; font-size: 27px; font-weight: 700; line-height: 34px; color: var(--ink); }
  .product__photo { position: absolute; }
  .product__photo--standby { left: 25px; top: 165px; width: 280px; height: 180px;
    background: linear-gradient(180deg, #f4f4f4 0%, #e6e6e6 65%, #222 78%, #1a1a1a 100%); }
  .product__photo--prime { left: 0; top: 0; width: 215px; height: 355px;
    background: linear-gradient(180deg, #e9e9e9 0%, #d7d7d7 45%, #2a2a2a 62%, #3a3a3a 100%); }
  .features { position: absolute; }
  .features__title { font-size: 15px; font-weight: 500; color: var(--ink); margin-bottom: 18px; }
  .features__list { list-style: none; font-family: "Lato", sans-serif; font-size: 6.5px; line-height: 11px; color: var(--charcoal); }
  .features__list li { position: relative; padding-left: 9px; margin-bottom: 8px; }
  .features__list li svg { position: absolute; left: 0; top: 2px; width: 7px; height: 7px; }
  .page__number { position: absolute; bottom: 10px; font-size: 13px; color: var(--charcoal); }
  .page__bar { position: absolute; height: 20px; }
</style>
</head>
<body>

<section class="spread spread--cover">
  <article class="page back-cover">
    <div class="back-cover__band"></div>
    <div class="back-cover__frame"></div>
    <div class="back-cover__brand">
      <div class="brand"><span class="brand__mark"></span><span class="brand__name">Voltharrow Power</span></div>
    </div>
    <div class="back-cover__contact">
      <p class="back-cover__title">Contact Us</p>
      <p class="back-cover__line">4100 Harbor Park Ave, Lakeview 20418</p>
      <p class="back-cover__line">(555) 014-2290</p>
    </div>
  </article>

  <article class="page front-cover">
    <svg class="page__art" viewBox="0 0 520 400" aria-hidden="true">
      <path d="M0 40 Q20 10 80 0 L0 0 Z" fill="#f2b51c"/>
      <path d="M0 120 Q30 30 120 0 L90 0 Q20 40 0 90 Z" fill="#2b2b2b"/>
      <path d="M0 190 L520 190 L520 270 Q470 310 420 330 L0 330 Z" fill="#2b2b2b"/>
      <rect x="0" y="330" width="520" height="70" fill="#f7f7f7" opacity=".9"/>
      <path d="M330 400 Q470 350 520 230 L520 400 Z" fill="#f2b51c"/>
    </svg>
    <div class="front-cover__photo" role="img" aria-label="Photo of a trailer-mounted diesel generator in a white enclosure"></div>
    <div class="front-cover__brand">
      <div class="brand"><span class="brand__mark"></span><span class="brand__name">Voltharrow Power</span></div>
    </div>
    <h1 class="front-cover__title">DISTRIBUTOR<br>PROGRAM<br>GUIDE</h1>
    <p class="front-cover__sub">Diesel Generators | Alternators | Parts</p>
    <div class="highlights">
      <div class="highlight">
        <svg viewBox="0 0 24 24" fill="none" stroke="#4a4546" stroke-width="1.4"><circle cx="12" cy="7" r="4"/><path d="M4 21c0-5 4-8 8-8s8 3 8 8"/></svg>
        Team of Experts
      </div>
      <div class="highlight">
        <svg viewBox="0 0 24 24" fill="none" stroke="#4a4546" stroke-width="1.4"><circle cx="12" cy="12" r="9"/><path d="M12 7v5l3 2"/></svg>
        Same Day Urgency
      </div>
      <div class="highlight">
        <svg viewBox="0 0 24 24" fill="none" stroke="#4a4546" stroke-width="1.4"><circle cx="12" cy="12" r="4"/><path d="M12 2v4M12 18v4M2 12h4M18 12h4M5 5l3 3M16 16l3 3M5 19l3-3M16 8l3-3"/></svg>
        100% Original
      </div>
    </div>
  </article>
</section>

<section class="spread spread--products">
  <article class="page product product--standby">
    <header class="section-head">
      <span class="section-head__rule" style="width:34px"></span>
      <h2 class="section-head__text">Our <strong>Products</strong></h2>
      <span class="section-head__rule" style="flex:1"></span>
    </header>
    <div class="product__block" style="left:0;top:72px"></div>
    <h3 class="product__name" style="left:115px;top:66px">Standby<br>Generators</h3>
    <div class="product__photo product__photo--standby" role="img" aria-label="Photo of a 100 kW standby diesel generator in a white enclosure"></div>
    <div class="features" style="left:320px;top:165px">
      <p class="features__title">FEATURES</p>
      <ul class="features__list">
        <li><svg viewBox="0 0 8 8"><path d="M1 4l2 2 4-5" stroke="#2b2b2b" stroke-width="1.4" fill="none"/></svg>Lorem ipsum dolor sit amet, consectetur<br>adipiscing elit, sed do eiusmod tempor incididunt</li>
        <li><svg viewBox="0 0 8 8"><path d="M1 4l2 2 4-5" stroke="#2b2b2b" stroke-width="1.4" fill="none"/></svg>Lorem ipsum dolor sit amet, consectetur<br>adipiscing elit, sed do eiusmod tempor incididunt</li>
        <li><svg viewBox="0 0 8 8"><path d="M1 4l2 2 4-5" stroke="#2b2b2b" stroke-width="1.4" fill="none"/></svg>Lorem ipsum dolor sit amet, consectetur<br>adipiscing elit, sed do eiusmod tempor incididunt</li>
        <li><svg viewBox="0 0 8 8"><path d="M1 4l2 2 4-5" stroke="#2b2b2b" stroke-width="1.4" fill="none"/></svg>Lorem ipsum dolor sit amet, consectetur<br>adipiscing elit, sed do eiusmod tempor incididunt</li>
      </ul>
    </div>
    <span class="page__number" style="left:18px">06</span>
    <div class="page__bar" style="left:205px;right:0;bottom:6px;background:var(--ink)"></div>
  </article>

  <article class="page product product--prime">
    <div class="product__photo product__photo--prime" role="img" aria-label="Photo of a trailer-mounted prime diesel generator"></div>
    <h3 class="product__name" style="left:250px;top:78px">Prime<br>Generators</h3>
    <div class="product__block" style="right:0;top:88px;width:62px;background:var(--gold)"></div>
    <div class="features" style="left:250px;top:172px">
      <p class="features__title">FEATURES</p>
      <ul class="features__list">
        <li><svg viewBox="0 0 8 8"><path d="M1 4l2 2 4-5" stroke="#2b2b2b" stroke-width="1.4" fill="none"/></svg>Lorem ipsum dolor sit amet, consectetur<br>adipiscing elit, sed do eiusmod tempor incididunt</li>
        <li><svg viewBox="0 0 8 8"><path d="M1 4l2 2 4-5" stroke="#2b2b2b" stroke-width="1.4" fill="none"/></svg>Lorem ipsum dolor sit amet, consectetur<br>adipiscing elit, sed do eiusmod tempor incididunt</li>
        <li><svg viewBox="0 0 8 8"><path d="M1 4l2 2 4-5" stroke="#2b2b2b" stroke-width="1.4" fill="none"/></svg>Lorem ipsum dolor sit amet, consectetur<br>adipiscing elit, sed do eiusmod tempor incididunt</li>
        <li><svg viewBox="0 0 8 8"><path d="M1 4l2 2 4-5" stroke="#2b2b2b" stroke-width="1.4" fill="none"/></svg>Lorem ipsum dolor sit amet, consectetur<br>adipiscing elit, sed do eiusmod tempor incididunt</li>
      </ul>
    </div>
    <div class="page__bar" style="left:0;width:300px;bottom:12px;background:var(--gold)"></div>
    <span class="page__number" style="right:18px">07</span>
  </article>
</section>

</body>
</html>
```